KLORA product web page

We need a new web design for our KLORA product page. You can find more information about the project on the current web site - www.klora.example

What we need from a new design (uncoded):
- landing pages + template
- all information on one page
- the design should be focused on the product - light bulb + app
- web site should be with some dynamics like a background with parallax effect in the current version
- fonts should be chosen
- a number of illustrations should be designed

Here is schema for a new design: https://files.examplehost.net/d/draw-7QpX2mLk9RtYv4Hs/edit

Here is a document with all texts for a new design: https://files.examplehost.net/d/doc-3WnZ8bJf5KcUe1Ga/edit

Illustrations to use:
v1 - https://files.examplehost.net/f/fold-A1kT9pQw2ZxR
v2 - https://files.examplehost.net/f/fold-B7mH4sLv6YcN

phones screens: https://files.examplehost.net/f/fold-C3rJ8dKe1WuP

KLORA logo: https://files.examplehost.net/f/fold-D5nF2gTb9XoM
Updates

I forgot to add the definition text "KLORA - is.." to the document with texts. Sorry, my mistake.

Target Market(s)

25-45 year old adults who are interested in "smart" devices for their health.

Industry/Entity Type

Brintel

Colors

Designer to choose colors to be used in the design.

Requirements
Must have
• - landing pages + template
- fonts should be chosen

```html
<!DOCTYPE html>
<html lang="en">
<head>
<meta charset="utf-8">
<title>KLORA – smart lighting for your health</title>
<link rel="stylesheet" href="https://fonts.googleapis.com/css2?family=Open+Sans:wght@300;400;600;700&display=swap">
<style>
:root{
  --blue:#1a8fd0;
  --blue-deep:#0f6fa8;
  --blue-dark:#0b5e8f;
  --green:#1f9a66;
  --charcoal:#2f2f31;
  --ink:#333;
  --muted:#777;
  --white:#fff;
  --yellow:#f5c51c;
  --orange:#eea93a;
  --olive:#8ea51d;
  --purple:#5a2b87;
  --light:#f2f2f2;
  --dark-btn:#262626;
}
*{box-sizing:border-box;margin:0;padding:0}
html,body{width:1200px;height:5070px;overflow:hidden}
body{font-family:"Open Sans",Arial,sans-serif;color:var(--ink);background:var(--white);position:relative}
section,header,footer{position:absolute;left:0;width:1200px;overflow:hidden}
.abs{position:absolute}
.btn{position:absolute;display:flex;align-items:center;justify-content:center;font-size:15px;color:var(--white);font-weight:400}
.fill{position:absolute;inset:0}
.dots{position:absolute;right:36px;display:flex;flex-direction:column;gap:14px}
.dots span{width:12px;height:12px;border-radius:50%;border:2px solid currentColor}
.dots span.on{background:currentColor}
h2.section-title{position:absolute;font-weight:400;font-size:34px;line-height:1.2}
.copy{position:absolute;font-size:13px;line-height:1.65}
.copy p+p{margin-top:18px}

/* header */
.site-header{top:0;height:90px;background:var(--white)}
.brand{left:78px;top:20px;font-size:40px;font-weight:700;color:var(--blue);letter-spacing:2px}
.nav{right:78px;top:30px;display:flex;gap:34px;align-items:center;font-size:14px;color:var(--blue)}
.nav .preorder{background:var(--charcoal);color:var(--white);padding:8px 18px;font-size:14px}

/* hero */
.hero{top:90px;height:570px}
.hero-bg{background:radial-gradient(circle at 83% 58%,#fffbe8 0,#d9d2b6 6%,#5a544a 20%,#2b2b2b 42%,#1e1e1e 100%)}
.hero h1{left:78px;top:135px;font-weight:300;font-size:46px;line-height:1.15;color:var(--white)}
.hero .lead{left:78px;top:262px;width:560px;font-size:21px;line-height:1.45;color:var(--white);font-weight:300}
.hero .pre{left:78px;top:373px;width:160px;height:44px;background:var(--blue)}
.hero .disc{left:263px;top:373px;width:160px;height:44px;background:var(--yellow);color:var(--ink)}
.hero .down{left:570px;top:420px}
.hero .arrow-l{left:18px;top:240px}
.hero .arrow-r{right:18px;top:240px}

/* green band */
.intro-band{top:660px;height:110px;background:var(--green)}
.intro-band .copy{left:78px;top:25px;width:720px;font-size:16px;line-height:1.5;color:var(--white)}
.intro-band .btn{left:872px;top:33px;width:170px;height:44px;background:var(--dark-btn)}

/* what we do */
.what{top:770px;height:673px;background:var(--charcoal);color:var(--white)}
.what h2{width:100%;text-align:center;top:70px;font-size:40px;font-weight:600}
.what .sub{width:100%;text-align:center;top:130px;font-size:14px}
.card{position:absolute;top:213px;width:300px;height:403px;background:var(--white);border-radius:6px;color:var(--ink);text-align:center}
.card .icon{position:absolute;left:20px;top:17px;width:260px;height:140px;background:var(--blue);border-radius:4px;display:flex;align-items:center;justify-content:center}
.card h3{position:absolute;top:205px;width:100%;font-size:20px;font-weight:400}
.card p{position:absolute;top:240px;left:22px;right:22px;font-size:12px;line-height:1.55;color:var(--muted)}
.card.c1{left:81px}.card.c2{left:460px}.card.c3{left:831px}
.what .dots{top:200px;color:var(--white)}

/* app */
.app{top:1443px;height:637px;background:radial-gradient(circle at 28% 45%,#2aa9e6 0,var(--blue) 35%,var(--blue-deep) 100%);color:var(--white)}
.app .visual{left:100px;top:100px;width:360px;height:430px;border-radius:20px;background:radial-gradient(circle at 30% 30%,#fff 0,#d8e7ef 18%,#4b5660 45%,rgba(30,30,30,.0) 75%)}
.app h2{left:558px;top:140px;color:var(--white)}
.app .copy{left:568px;top:210px;width:560px}
.app .btn{left:568px;top:450px;width:182px;height:44px;background:var(--dark-btn)}
.app .dots{top:165px;color:var(--white)}

/* color */
.colour{top:2080px;height:540px;background:var(--purple);color:var(--white)}
.colour h2{left:81px;top:120px;color:var(--white)}
.colour .copy{left:81px;top:190px;width:540px}
.colour .btn{left:81px;top:354px;width:182px;height:42px;background:var(--dark-btn)}
.colour .visual{left:740px;top:110px;width:400px;height:340px;background:radial-gradient(circle at 75% 22%,#f3e24a 0,#c2b54a 12%,transparent 34%),radial-gradient(circle at 30% 25%,#6fe0ff 0,#48a8d5 12%,transparent 32%),radial-gradient(circle at 45% 50%,#ff4545 0,#c62a2a 9%,transparent 24%),radial-gradient(circle at 55% 70%,#3a3a3a 0,transparent 60%)}
.colour .dots{top:145px;color:var(--white)}

/* health */
.health{top:2620px;height:580px}
.health-bg{background:linear-gradient(90deg,#6c5a48 0,#8a7a66 18%,#cfc7bb 42%,#f2f0ec 55%,#f7f6f4 100%)}
.health h2{left:558px;top:135px;color:#444;font-weight:300;font-size:38px}
.health .sub{left:558px;top:195px;font-size:16px;color:#555}
.ticks{position:absolute;list-style:none;font-size:13px;line-height:1.6;color:#444}
.ticks li{position:relative;padding-left:24px;margin-bottom:8px}
.ticks li svg{position:absolute;left:0;top:4px}
.health .ticks{left:558px;top:250px;width:560px}
.health .btn{left:551px;top:432px;width:186px;height:40px;background:var(--olive)}
.health .dots{top:40px;color:var(--blue)}

/* tech */
.tech{top:3200px;height:600px;background:linear-gradient(180deg,#fafafa 0,var(--light) 100%)}
.tech h2{left:101px;top:110px;color:#333}
.tech .ticks{left:101px;top:185px;width:560px;font-size:12px;color:#555}
.tech .ticks li{margin-bottom:16px}
.tech .btn{left:101px;top:467px;width:152px;height:45px;background:var(--orange)}
.tech .visual{left:770px;top:45px;width:380px;height:540px;background:radial-gradient(circle at 75% 14%,#fff 0,#bbb 9%,#333 20%,transparent 30%),linear-gradient(160deg,transparent 0,transparent 40%,#d9dee3 41%,#c5ccd3 100%)}
.tech .dots{top:60px;color:var(--blue)}

/* lighting design */
.design{top:3800px;height:545px;color:var(--white)}
.design-bg{background:radial-gradient(circle at 20% 40%,#9a8f82 0,#5a4a3c 22%,#3a2a22 50%,#2a1d18 100%)}
.design h2{left:558px;top:130px;color:var(--white)}
.design .copy{left:568px;top:200px;width:560px}
.design .btn{left:600px;top:408px;width:186px;height:40px;background:var(--orange)}

/* get */
.get{top:4345px;height:665px;background:linear-gradient(180deg,#1a9ad8 0,var(--blue) 100%);color:var(--white)}
.get h2{left:91px;top:160px;color:var(--white)}
.get .sub{left:91px;top:230px;font-size:12px;font-weight:700}
.signup{position:absolute;left:91px;top:296px;display:flex}
.signup .field{width:467px;height:67px;background:var(--white);color:#999;font-size:20px;display:flex;align-items:center;padding-left:22px}
.signup .go{width:67px;height:67px;background:var(--blue-dark);display:flex;align-items:center;justify-content:center}
.get .copy{left:91px;top:400px;width:560px;font-size:13px}
.get .up{left:581px;top:546px}
.get .visual{left:790px;top:50px;width:340px;height:580px;background:radial-gradient(ellipse at 50% 40%,#fff 0,#d6f1ff 18%,rgba(255,255,255,.2) 40%,transparent 62%)}
.get .dots{top:100px;color:var(--white)}

/* footer */
.site-footer{top:5010px;height:60px;background:var(--white);font-size:12px;color:#555}
.site-footer .legal{left:91px;top:22px}
.site-footer .social-label{left:860px;top:22px}
.site-footer .social{left:968px;top:14px;display:flex;gap:14px}
.site-footer .social span{width:32px;height:32px;border-radius:50%;background:#444}
</style>
</head>
<body>

<header class="site-header">
  <div class="abs brand">KLORA</div>
  <nav class="abs nav">
    <span class="preorder">PRE-ORDER</span><span>BLOG</span><span>CONTACTS</span><span>RU</span>
  </nav>
</header>

<section class="hero">
  <div class="fill hero-bg" role="img" aria-label="Dark interior photograph with a glowing KLORA LED bulb hanging on the right"></div>
  <svg class="abs arrow-l" width="16" height="30" viewBox="0 0 16 30"><path d="M14 2 2 15l12 13" fill="none" stroke="#fff" stroke-width="3"/></svg>
  <svg class="abs arrow-r" width="16" height="30" viewBox="0 0 16 30"><path d="M2 2l12 13L2 28" fill="none" stroke="#fff" stroke-width="3"/></svg>
  <h1 class="abs">KLORA is for your<br>comfort</h1>
  <p class="abs lead">Choose a scene for setting the alarm and improve your sleep naturally. KLORA lighting system</p>
  <div class="btn pre">Pre - order</div>
  <div class="btn disc">Discover more</div>
  <svg class="abs down" width="76" height="76" viewBox="0 0 76 76"><circle cx="38" cy="38" r="35" fill="none" stroke="#fff" stroke-width="3"/><path d="M24 32l14 14 14-14" fill="none" stroke="#fff" stroke-width="4"/></svg>
</section>

<section class="intro-band">
  <p class="copy">KLORA is the right lighting designed especialy for your health and comfort: a smart true color wireless enabled LED light bulb.</p>
  <div class="btn">Read more</div>
</section>

<section class="what">
  <h2 class="abs">What We do</h2>
  <p class="abs sub">10 preset moods provide positive impact on your health.</p>
  <div class="card c1">
    <div class="icon"><svg width="76" height="76" viewBox="0 0 76 76" fill="#fff"><rect x="0" y="0" width="20" height="20" rx="3"/><rect x="28" y="0" width="20" height="20" rx="3"/><rect x="56" y="0" width="20" height="20" rx="3"/><rect x="0" y="28" width="20" height="20" rx="3"/><rect x="28" y="28" width="20" height="20" rx="3"/><rect x="56" y="28" width="20" height="20" rx="3"/><rect x="0" y="56" width="20" height="20" rx="3"/><rect x="28" y="56" width="20" height="20" rx="3"/><rect x="56" y="56" width="20" height="20" rx="3"/></svg></div>
    <h3>KLORA APP</h3>
    <p>KLORA Application allows you to control each lightbulb at home. Manage your lighting by creating functional groups and adding/excluding lightbulbs. Correctly matched lighting will help you work more productively and relax to the outmost.</p>
  </div>
  <div class="card c2">
    <div class="icon"><svg width="90" height="80" viewBox="0 0 90 80"><path d="M45 4C20 4 4 20 4 40s16 36 38 36c8 0 8-8 4-12s-2-10 6-10h12c14 0 22-8 22-20C86 16 68 4 45 4z" fill="none" stroke="#fff" stroke-width="4"/><circle cx="24" cy="38" r="6" fill="#fff"/><circle cx="34" cy="20" r="6" fill="#fff"/><circle cx="56" cy="18" r="6" fill="#fff"/><circle cx="70" cy="34" r="6" fill="#fff"/></svg></div>
    <h3>KLORA &nbsp;COLOR</h3>
    <p>Experiment with millions of colors! Pick any color from the screen of your mobile lightbulb KLORA can transform conventional lighting into the night lights of Seattle or bring in the rich summer hues of Provence. Enliven your fantasies or raise your best memories in one click.</p>
  </div>
  <div class="card c3">
    <div class="icon"><svg width="60" height="90" viewBox="0 0 60 90" fill="none" stroke="#fff" stroke-width="4"><path d="M30 4C15 4 6 15 6 28c0 10 6 16 10 22 3 5 4 9 4 12h20c0-3 1-7 4-12 4-6 10-12 10-22C54 15 45 4 30 4z"/><path d="M20 70h20M22 78h16M26 86h8"/></svg></div>
    <h3>KLORA</h3>
    <p>KLORA lightbulb is a 80W incandescent equivalent that transforms your visual environment. E27 socket, no need to change anything. Easy way to home automation at hand, and you can still use those switches.</p>
  </div>
  <div class="dots"><span></span><span></span><span></span><span class="on"></span><span></span><span></span></div>
</section>

<section class="app">
  <div class="abs visual" role="img" aria-label="KLORA bulb glowing white next to a phone showing the KLORA app"></div>
  <h2 class="section-title">✓ KLORA App</h2>
  <div class="copy">
    <p>KLORA Application allows you to control each lightbulb at home. Manage your lighting by creating functional groups and adding/excluding lightbulbs. Correctly matched lighting will help you work more productively and relax to the outmost.</p>
    <p>Create light scenes and adapt them to your needs. KLORA app memorizes your favorite moods, so that you can use your settings anytime.</p>
    <p>Play with million colors and adjust the brightness of your home lighting. KLORA works on phones and tablets.</p>
  </div>
  <div class="btn">Discover more</div>
  <div class="dots"><span></span><span></span><span></span><span class="on"></span><span></span><span></span></div>
</section>

<section class="colour">
  <h2 class="section-title">✓ KLORA and color</h2>
  <p class="copy">Experiment with millions of colors! Pick any color from the screen of your mobile device and enjoy the ambience. LED lightbulb KLORA can transform conventional lighting into the night lights of Seattle or bring in the rich summer hues of Provence. Enliven your fantasies or raise your best memories in one click. Change the atmosphere around you by changing colors. You will literally see the world in a new light.</p>
  <div class="btn">Discover more</div>
  <div class="abs visual" role="img" aria-label="Three KLORA bulbs glowing cyan, yellow and red"></div>
  <div class="dots"><span></span><span></span><span></span><span class="on"></span><span></span><span></span></div>
</section>

<section class="health">
  <div class="fill health-bg" role="img" aria-label="Desk lamp photograph with a hand fitting a KLORA bulb, bookshelf behind"></div>
  <h2 class="section-title">KLORA and health</h2>
  <p class="abs sub">Lorem Ipsum Dolor Sit amet and typesetting industry and lispum send.</p>
  <ul class="ticks">
    <li><svg width="14" height="12" viewBox="0 0 14 12"><path d="M1 6l4 4 8-9" fill="none" stroke="#1a8fd0" stroke-width="2.5"/></svg>The right light for your vision: optimized color rendering and color temperature</li>
    <li><svg width="14" height="12" viewBox="0 0 14 12"><path d="M1 6l4 4 8-9" fill="none" stroke="#1a8fd0" stroke-width="2.5"/></svg>KLORA creates the appropriate lighting for concentration and relaxation considering your emotional and physical state</li>
    <li><svg width="14" height="12" viewBox="0 0 14 12"><path d="M1 6l4 4 8-9" fill="none" stroke="#1a8fd0" stroke-width="2.5"/></svg>Lighting for healthy sleep and natural awakening: set your alarm clock to light up gradually, stay in harmony with your biological rhythms.</li>
  </ul>
  <div class="btn">Read more</div>
  <div class="dots"><span class="on"></span><span></span><span class="on"></span><span></span><span class="on"></span><span></span><span class="on"></span></div>
</section>

<section class="tech">
  <h2 class="section-title">KLORA technical specifications</h2>
  <ul class="ticks">
    <li><svg width="12" height="10" viewBox="0 0 14 12"><path d="M1 6l4 4 8-9" fill="none" stroke="#999" stroke-width="2.5"/></svg>KLORA lightbulb is a 80W incandescent equivalent that transforms your visual environment.</li>
    <li><svg width="12" height="10" viewBox="0 0 14 12"><path d="M1 6l4 4 8-9" fill="none" stroke="#999" stroke-width="2.5"/></svg>E27 socket; no need to change anything. Easy way to home automation at hand. And yes, you can still use those switches.</li>
    <li><svg width="12" height="10" viewBox="0 0 14 12"><path d="M1 6l4 4 8-9" fill="none" stroke="#999" stroke-width="2.5"/></svg>12.5W (110 - 230V 50Hz), 1000lm+ energy efficient LED lightbulb KLORA shines brighter than others and saves energy.</li>
    <li><svg width="12" height="10" viewBox="0 0 14 12"><path d="M1 6l4 4 8-9" fill="none" stroke="#999" stroke-width="2.5"/></svg>2700-5500K: You are not limited in your choice of color temperature. Turn on warm or cold light depending on your activities.</li>
    <li><svg width="12" height="10" viewBox="0 0 14 12"><path d="M1 6l4 4 8-9" fill="none" stroke="#999" stroke-width="2.5"/></svg>Compatibility:</li>
  </ul>
  <div class="btn">Read more</div>
  <div class="abs visual" role="img" aria-label="KLORA bulb above a phone showing the bedroom lighting screen"></div>
  <div class="dots"><span></span><span class="on"></span><span></span><span class="on"></span><span></span><span class="on"></span><span></span></div>
</section>

<section class="design">
  <div class="fill design-bg" role="img" aria-label="Close-up photograph of a KLORA bulb on a dark warm background"></div>
  <h2 class="section-title">✓ Lighting Design</h2>
  <div class="copy">
    <p>Wireless lightbulbs with smart connectivity help you implement the concept of the smart home. KLORA makes it affordable. Real lighting design at your place, couldn't have been simpler.</p>
    <p>Create optimal lighting for each functional area - set the perfect light for your kitchen, living room and nursery. Name individual lightbulbs or groups of them, set your color mood, pick a palette for each room. Stay informed of every smart lightbulb condition.</p>
  </div>
  <div class="btn">Discover more</div>
</section>

<section class="get">
  <h2 class="section-title">Get your KLORA</h2>
  <p class="abs sub">Enter your e-mail and we will notify you when it's available</p>
  <div class="signup">
    <div class="field">E-mail address</div>
    <div class="go"><svg width="24" height="18" viewBox="0 0 24 18"><rect x="1" y="1" width="22" height="16" fill="none" stroke="#fff" stroke-width="2"/><path d="M1 1l11 9 11-9" fill="none" stroke="#fff" stroke-width="2"/></svg></div>
  </div>
  <p class="copy">Wireless lightbulbs with smart connectivity help you implement the concept of the smart home. KLORA makes it affordable. Real lighting design at your place, couldn't have been simpler. Create optimal lighting for each functional area - set the perfect light for your kitchen, living room and nursery.</p>
  <svg class="abs up" width="76" height="76" viewBox="0 0 76 76"><circle cx="38" cy="38" r="35" fill="none" stroke="#fff" stroke-width="3"/><path d="M24 44l14-14 14 14" fill="none" stroke="#fff" stroke-width="4"/></svg>
  <div class="abs visual" role="img" aria-label="KLORA bulb glowing bright white"></div>
  <div class="dots"><span></span><span></span><span class="on"></span><span></span><span></span><span></span></div>
</section>

<footer class="site-footer">
  <span class="abs legal">©Lumenfold Ltd. 2014</span>
  <span class="abs social-label">Socialise With us</span>
  <div class="abs social"><span></span><span></span><span></span><span></span></div>
</footer>

</body>
</html>
```